Business Card Design Project

Business Card
We are rebranding with a new logo
Industry/Entity Type
Business
Contact Information for Business Card
Dennis Morvale +61 487215963 dennis@quorv.com.au P.O. Box 872 Fernlow QLD 4309
Requirements
Must have
- Logo

```html
<!DOCTYPE html>
<html lang="en">
<head>
<meta charset="utf-8">
<title>Quorv International – Business Card</title>
<link rel="stylesheet" href="https://fonts.googleapis.com/css2?family=Open+Sans:wght@400;600;700&display=swap">
<style>
  :root {
    --backdrop: #2a2a2a;
    --card: #f6f6f6;
    --brand-blue: #1a86c4;
    --brand-orange: #ef7d1a;
    --text-grey: #555a5e;
    --divider: #cfcfcf;
  }
  * { box-sizing: border-box; margin: 0; padding: 0; }
  html, body {
    width: 1200px;
    height: 915px;
    overflow: hidden;
    background: var(--backdrop);
    font-family: "Open Sans", Arial, sans-serif;
  }
  .canvas {
    width: 1200px;
    height: 915px;
    display: flex;
    align-items: center;
    justify-content: center;
  }
  .business-card {
    width: 900px;
    height: 514px;
    background: var(--card);
    position: relative;
    display: flex;
    align-items: center;
  }
  .brand-side {
    width: 480px;
    display: flex;
    align-items: center;
    justify-content: center;
    gap: 16px;
  }
  .brand-dot {
    width: 30px;
    height: 30px;
    border-radius: 50%;
    background: var(--brand-orange);
  }
  .brand-name {
    font-weight: 600;
    font-size: 40px;
    line-height: 1;
    color: var(--brand-blue);
  }
  .divider {
    width: 2px;
    height: 196px;
    background: var(--divider);
  }
  .contact-side {
    padding-left: 34px;
    color: var(--text-grey);
  }
  .person-name {
    font-weight: 700;
    font-size: 22px;
    color: var(--brand-blue);
    letter-spacing: 0.3px;
    margin-bottom: 22px;
  }
  .postal-address {
    font-style: normal;
    font-size: 18px;
    line-height: 1.35;
    margin-bottom: 10px;
  }
  .contact-list { list-style: none; font-size: 18px; line-height: 1.4; }
  .contact-list li { display: flex; align-items: center; gap: 12px; }
  .contact-icon { width: 16px; height: 16px; flex: none; fill: var(--brand-blue); }
</style>
</head>
<body>
<main class="canvas">
  <article class="business-card">
    <div class="brand-side">
      <span class="brand-dot"></span>
      <span class="brand-name">Quorv International</span>
    </div>
    <div class="divider"></div>
    <div class="contact-side">
      <h1 class="person-name">DENNIS MORVALE</h1>
      <address class="postal-address">P.O. Box 872<br>Fernlow QLD 4309</address>
      <ul class="contact-list">
        <li>
          <svg class="contact-icon" viewBox="0 0 16 16" aria-hidden="true"><path d="M2 5c0-2 2-3 6-3s6 1 6 3v1h-3V5H5v1H2z"/><path d="M4 7h8l2 7H2z"/><circle cx="8" cy="10.5" r="1.6" fill="#f6f6f6"/></svg>
          <span>+61 487215963</span>
        </li>
        <li>
          <svg class="contact-icon" viewBox="0 0 16 16" aria-hidden="true"><rect x="1" y="3" width="14" height="10" rx="1"/><path d="M1.5 3.5 8 9l6.5-5.5" fill="none" stroke="#f6f6f6" stroke-width="1.3"/></svg>
          <span>dennis@quorv.com.au</span>
        </li>
        <li>
          <svg class="contact-icon" viewBox="0 0 16 16" aria-hidden="true"><circle cx="8" cy="8" r="7"/><path d="M4 5c2 0 3 1 2 3s1 3 0 4M10 3c0 2 2 2 3 4" fill="none" stroke="#f6f6f6" stroke-width="1.3"/></svg>
          <span>www.quorv.com.au</span>
        </li>
      </ul>
    </div>
  </article>
</main>
</body>
</html>
```